DeskHarbor | A Happiness Company

We need to Develop a Sales Brochure for a coworking space:
1. About DeskHarbor
2. Location
3. Cards to Show Benefits
4. Floor Plan and Pictures
5. Pricing Card

Jersey City Coworking/Shared Office Space, Steps from Millbrook LINK
Impress your clients. Stimulate your creativity. Unleash your inner genius.
DeskHarbor is Jersey City’s newest premier coworking and shared office space,

home to:

 Entrepreneurs
 Visionaries
 Freelancers
 Consultants
 Telecommuters
 Startups
 + More

Here you’ll have access to everything you need in order to work efficiently, productively, happily and healthily. Essentials, Amenities and Resources
 Furnished office space with 24/7 access
 Conference rooms and meeting spaces
 Networking events and educational workshops
 Business support
 Ultra-High Speed Internet
 Secure WiFi
 Print + Copy + Scan
 Mail service and business address
 White boards and office supplies
 Gourmet teas and coffees
 Kitchen stocked with healthy snacks
 + More

Member Discounts
 Hotel
 Travel
 Car Rental
 Cloud and server
 + More

Our Values

Collaboration, Community, Happiness, Wellness, Growth
Bonus: Our short-term funding program offers financial support to help your business reach its next milestone.
Location and Pricing
DeskHarbor is located at 248 Garden Crest Lane in Jersey City, a prestigious
address on the banks of the Hudson River, just minutes from the Barrow Causeway and steps from the Millbrook LINK station.
1. The cover of the brochure should create excitement to open the folder. Do not create a trifold. We are a very high end office space not a medical office. The size of the paper, does not have to be standard. Think card stock, matt or Glossy or Both

2. On Opening the Brochure - The First Page is to educate my client with a art, color and words
3. Page 2,3,4 and 5Is about Inspiration and explanation: I am thinking that they should be cards of detail:
1. Orange: Vision - Consider a theme of Innovation, High Performance, Fun, Value from action, resources, impulse
2. Gold: Details: Orange: Vision - Consider a theme of Authority and Leadership. The duty to Shine, the leader being the backbone of the group. Practial, values of home, status, security, and traditions
3. Blue: Encourage and support, A peacemaker, Think about themes of caring, counseling, nurturing, Idealistic and sympathetic. This is about contribution
4. Green: The Independent thinker, seeking knowledge, intelligence, justice and insight. About the details

The message on these cards should be similar but at various levels of detail

The 5th Card is about Floor Plans - You are not responsible for it this card. Just the Look of how the card should look like

The 6th Card is about pricing
Updates

Reason: Only 1 designer has provided a decent design. Most of the submissions were recycled and not in line. Please extend by 4 weeks.

Target Market(s)

- Technology Companies (10 people or less)
- Entrepreneurs (2 People)
- Freelancers (1 People)
- small size Technology Company (5 people or less)

Industry/Entity Type

It Company

Font styles to use
Other font styles liked:
• Caviar Dreams and Sans Serif

Requirements
Must have
• - Pictures
• - Details
• - Inspiration
• - FLoor plans
• - Questions and Value
• - Minimal
• Why would they want to buy your product? 
• What's the most important thing it can do for them?
• What is the most important problem your product or service can solve for them?
• To be effective, your brochure needs to get attention, get the prospect interested enough to read further, raise their desire for the product or service, and get them to take a specific action such as buy now, call and make an appointment, return a post card.
Nice to have
• I am open to design - be inspirational
• Should be clear
• They are interested in themselves and/or their own businesses. To get their attention, your brochure needs to focus on the benefits they will enjoy by making a purchase from you.
Should not have
• Cannot be too Salesy
• No Stock pictures
• Don't put a picture of your building on the cover of the brochure
• The only thing they care about is whether or not your products meet their needs.

```html
<!DOCTYPE html>
<html lang="en">
<head>
<meta charset="utf-8">
<title>DeskHarbor Brochure – Inside Spread</title>
<link rel="stylesheet" href="https://fonts.googleapis.com/css2?family=Comfortaa:wght@400;600&family=Josefin+Sans:wght@300&family=Roboto+Condensed:wght@300;400&display=swap">
<style>
  :root {
    --backdrop: #e9e6e1;
    --orange: #e0701e;
    --orange-deep: #d4601a;
    --orange-light: #f08a2c;
    --page-light: #f1f1f1;
    --page-shade: #e2e2e2;
    --ink: #4a4a4a;
    --ink-soft: #6a6a6a;
    --photo-sky: #5f87a8;
    --photo-room: #8a8f8c;
    --photo-floor: #3c3a36;
    --white: #ffffff;
  }
  * { box-sizing: border-box; margin: 0; padding: 0; }
  html, body { width: 1200px; height: 750px; overflow: hidden; }
  body { background: var(--backdrop); position: relative; font-family: "Roboto Condensed", sans-serif; }

  .spread {
    position: absolute; left: 40px; top: 173px;
    width: 1120px; height: 404px;
    display: flex;
    box-shadow: 0 12px 28px rgba(0,0,0,.25);
  }
  .page { position: relative; width: 560px; height: 404px; overflow: hidden; }

  /* Inside cover */
  .inside-cover__photo {
    position: absolute; inset: 0 0 60px 0;
    background:
      linear-gradient(180deg, rgba(255,255,255,.25) 0%, rgba(255,255,255,0) 40%),
      linear-gradient(180deg, var(--photo-sky) 0%, var(--photo-room) 55%, var(--photo-floor) 100%);
  }
  .inside-cover__title {
    position: absolute; left: 56px; top: 50px;
    font-family: "Josefin Sans", sans-serif; font-weight: 300;
    font-size: 18.5px; color: var(--white); letter-spacing: 0;
    white-space: nowrap;
  }
  .inside-cover__rule {
    position: absolute; left: 40px; top: 82px; width: 470px; height: 3px;
    background-image: radial-gradient(circle, var(--orange-light) 1.2px, transparent 1.4px);
    background-size: 7px 3px;
  }
  .band {
    position: absolute; left: 0; right: 0; bottom: 0; height: 60px;
    background: linear-gradient(90deg, var(--orange-deep), var(--orange-light) 60%, var(--orange));
  }
  .band__nav {
    position: absolute; left: 109px; top: 10px;
    font-size: 9px; font-weight: 300; color: rgba(255,255,255,.85); white-space: nowrap;
  }
  .band__nav span { margin: 0 4px; }

  /* Page 3 */
  .page--intro { background: linear-gradient(90deg, var(--page-shade) 0%, var(--page-light) 12%, var(--page-light) 100%); }
  .intro__bulb { position: absolute; left: 158px; top: 83px; }
  .intro__body {
    position: absolute; left: 39px; top: 168px; width: 280px;
    font-size: 8.6px; line-height: 15px; color: var(--ink);
    text-align: justify;
  }
  .intro__body p + p { margin-top: 12px; }
  .checklist { position: absolute; left: 334px; top: 62px; width: 215px; }
  .checklist__title {
    font-family: "Comfortaa", sans-serif; font-weight: 600;
    font-size: 12px; color: var(--orange); margin-bottom: 5px;
    white-space: nowrap;
  }
  .checklist ul { list-style: none; }
  .checklist li {
    font-size: 7.4px; font-weight: 300; line-height: 10.8px; color: var(--ink-soft);
    padding-left: 13px; position: relative; white-space: nowrap;
  }
  .checklist li::before {
    content: "✓"; position: absolute; left: 0; top: 0;
    color: var(--orange); font-weight: 700;
  }
  .checklist__sub { font-size: 7.4px; font-weight: 300; color: var(--ink-soft); margin: 10px 0 1px; }
  .checklist__options { margin-top: 10px; }
</style>
</head>
<body>
  <div class="spread">
    <section class="page page--inside-cover">
      <div class="inside-cover__photo" role="img" aria-label="Photograph of a bright meeting room with a white table, orange and yellow chairs and floor-to-ceiling windows over the city"></div>
      <h2 class="inside-cover__title">CREATIVE GENIUS IN THE COWORKING SPACES</h2>
      <div class="inside-cover__rule"></div>
      <div class="band">
        <p class="band__nav">Work Efficiently, Productively, Happily &amp; Healthily<span>|</span>Essentials<span>|</span>Amenities<span>|</span>Resources</p>
      </div>
    </section>

    <section class="page page--intro">
      <svg class="intro__bulb" width="42" height="72" viewBox="0 0 42 72" role="img" aria-label="Glowing orange light bulb illustration">
        <defs>
          <radialGradient id="bulbGlow" cx="50%" cy="40%" r="60%">
            <stop offset="0" stop-color="#ffd27a"/>
            <stop offset=".6" stop-color="#f39a22"/>
            <stop offset="1" stop-color="#d4601a"/>
          </radialGradient>
        </defs>
        <ellipse cx="21" cy="22" rx="20" ry="21" fill="url(#bulbGlow)"/>
        <rect x="13" y="40" width="16" height="16" rx="3" fill="#e37a22"/>
        <rect x="13" y="55" width="16" height="12" rx="3" fill="#6b6b6b"/>
      </svg>

      <div class="intro__body">
        <p>DeskHarbor is Jersey City's newest premier coworking and shared office space. Whether you're a visionary entrepreneur, a full-time freelancer, an independent consultant, a telecommuter or a startup team, here you'll have access to everything you need in order to work efficiently, productively, happily and healthily.</p>
        <p>Our state-of-the-art rooms are quiet and put you in touch with your inner self giving you a chance to stay grounded, centered and unstoppable.</p>
      </div>

      <div class="checklist">
        <h3 class="checklist__title">Access to Everything You Need</h3>
        <ul>
          <li>Furnished office space with 24/7 access</li>
          <li>Conference rooms and meeting spaces</li>
          <li>Networking events and educational workshops</li>
          <li>Business support</li>
          <li>Ultra-High Speed Internet</li>
          <li>Secure WiFi</li>
          <li>Print + Copy + Scan</li>
          <li>Mail service and business address</li>
          <li>White boards and office supplies</li>
          <li>Gourmet teas and coffees</li>
          <li>Kitchen stocked with healthy snacks</li>
          <li>Plus Much More</li>
        </ul>
        <p class="checklist__sub">Member Discounts</p>
        <ul>
          <li>Hotel</li>
          <li>Travel</li>
          <li>Car Rental</li>
          <li>Cloud and server</li>
          <li>Plus Much More</li>
        </ul>
        <ul class="checklist__options">
          <li>Daily, Monthly &amp; Annual Options</li>
        </ul>
      </div>

      <div class="band"></div>
    </section>
  </div>
</body>
</html>
```